Road Construction Company needs business cards

We would like a new business card designed for our business.

We're a road construction company based in Qld, Australia.

Can the business card please have the following information on it.

Name: Warren Halbeck
Position: General Manager
Phone: 0472 915 348
Email: Warren.halbeck@tovrin.com.au
Address: 87 Marrow Ave, Pendlebay, QLD, 4023
Website: www.tovrin.com.au

Visually we'd like the card to be professional and simple.

Attached is our logo.

Our website is www.tovrin.com.au

Target Market(s)

Men aged 25-60

Contact Information for Business Card

As listed in project description

Font styles to use
Serif

Requirements
Must have
• Large logo on back of card

```html
<!DOCTYPE html>
<html lang="en">
<head>
<meta charset="utf-8">
<title>Tovrin Business Card</title>
<link href="https://fonts.googleapis.com/css2?family=Inter:wght@400;700;800&display=swap" rel="stylesheet">
<style>
  :root {
    --backdrop: #8e8e8e;
    --card: #1b1b1c;
    --blue-deep: #1262b4;
    --blue-bright: #2ba2da;
    --text-light: #f2f2f2;
  }
  * { margin: 0; padding: 0; box-sizing: border-box; }
  html, body {
    width: 1200px;
    height: 588px;
    overflow: hidden;
    background: var(--backdrop);
    font-family: "Inter", Arial, sans-serif;
  }
  .stage { position: relative; width: 1200px; height: 588px; }
  .card {
    position: absolute;
    width: 488px;
    height: 287px;
    background: var(--card);
    overflow: hidden;
  }
  .card-back { left: 87px; top: 141px; }
  .back-pattern {
    position: absolute;
    inset: 0;
    background:
      radial-gradient(ellipse at 85% 70%, rgba(70,70,70,0.55) 0%, rgba(70,70,70,0) 60%),
      linear-gradient(125deg, #080808 0%, #121212 38%, #262626 70%, #383838 100%);
  }
  .back-brand {
    position: absolute;
    inset: 0;
    display: flex;
    align-items: center;
    justify-content: center;
    font-size: 54px;
    font-weight: 800;
    letter-spacing: 3px;
    color: var(--blue-deep);
    line-height: 1;
  }
  .card-front { left: 622px; top: 143px; color: var(--text-light); }
  .brand-name {
    position: absolute;
    left: 23px;
    top: 24px;
    font-size: 38px;
    font-weight: 800;
    letter-spacing: 1px;
    color: var(--blue-deep);
    line-height: 1;
  }
  .person {
    position: absolute;
    right: 23px;
    top: 128px;
    text-align: right;
  }
  .person-name {
    font-size: 19px;
    font-weight: 700;
    color: var(--blue-bright);
    line-height: 1.2;
  }
  .person-role {
    font-size: 13.5px;
    font-weight: 400;
    margin-top: 2px;
  }
  .divider {
    position: absolute;
    left: 23px;
    right: 23px;
    top: 184px;
    height: 1px;
    background: var(--blue-bright);
  }
  .contact-list {
    position: absolute;
    left: 23px;
    top: 200px;
    list-style: none;
    font-size: 13.5px;
    line-height: 19px;
  }
  .contact-list li { display: flex; align-items: center; gap: 6px; }
  .contact-list svg { width: 10px; height: 10px; fill: var(--blue-deep); flex: none; }
  .address {
    position: absolute;
    right: 23px;
    top: 200px;
    text-align: right;
    font-size: 13.5px;
    line-height: 19px;
    font-style: normal;
  }
  .accent-band {
    position: absolute;
    left: 0;
    right: 0;
    bottom: 0;
    height: 11px;
    background: linear-gradient(90deg, var(--blue-deep), var(--blue-bright));
  }
</style>
</head>
<body>
<main class="stage">
  <section class="card card-back">
    <div class="back-pattern" role="img" aria-label="Repeating brand mark pattern on dark background, fading from black to charcoal"></div>
    <div class="back-brand">TOVRIN</div>
  </section>

  <section class="card card-front">
    <div class="brand-name">TOVRIN</div>

    <div class="person">
      <div class="person-name">WARREN HALBECK</div>
      <div class="person-role">General Manager</div>
    </div>

    <div class="divider"></div>

    <ul class="contact-list">
      <li>
        <svg viewBox="0 0 10 10" aria-hidden="true"><path d="M2 0.5 L3.6 2.6 L2.7 3.6 Q3.6 5.6 6.4 7.3 L7.4 6.4 L9.5 8 L8.3 9.5 Q4.5 9.5 1.5 5.5 Q0.3 3.6 0.5 1.7 Z"/></svg>
        <span>0472 915 348</span>
      </li>
      <li>
        <svg viewBox="0 0 10 10" aria-hidden="true"><path d="M0 2 H10 V8.5 H0 Z M0.6 2.4 L5 5.6 L9.4 2.4 V3.3 L5 6.5 L0.6 3.3 Z" fill-rule="evenodd"/></svg>
        <span>Warren.halbeck@tovrin.com.au</span>
      </li>
      <li>
        <svg viewBox="0 0 10 10" aria-hidden="true"><circle cx="5" cy="5" r="4.7"/><path d="M3 2.5 Q4.5 3 4 4.5 Q2.5 5 2.8 6.8 Q1.2 5.5 1.3 3.8 Z M6.2 5.2 Q7.8 5 8.2 6.6 Q7.3 8.3 5.8 8.6 Q6.5 7 6.2 5.2 Z" fill="#1b1b1c"/></svg>
        <span>www.tovrin.com.au</span>
      </li>
    </ul>

    <address class="address">
      87 Marrow Ave<br>
      Pendlebay, QLD, 4023
    </address>

    <div class="accent-band"></div>
  </section>
</main>
</body>
</html>
```